Maple Roster Business Card for recruitment company

We are looking for a Business Card Design that incorporates our personal details and our busines name and logo. We are a specialized search consultancy that recruit Property and Construction professionals.
We would like a business card that stands out and is appealing to the Construction and Property industry as well.

Target Market(s)

people in the construction and property industry

Contact Information for Business Card

Business Name and logo

Font styles to use
Serif

Colors
0094D4
00A9DD
6FCCEA
C7EBF8
E9F6FB

Requirements
Must have
• Business name and logo as well as contact details
Should not have
• No photos of us please

```html
<!DOCTYPE html>
<html lang="en">
<head>
<meta charset="utf-8">
<title>Maple Roster — Business Card</title>
<link rel="stylesheet" href="https://fonts.googleapis.com/css2?family=Questrial&family=Mulish:wght@800&display=swap">
<style>
  :root {
    --navy: #08394f;
    --navy-deep: #052c3d;
    --navy-soft: #1b4c62;
    --ink: #2f3a40;
    --paper: #ffffff;
    --paper-shade: #ebebeb;
    --mark-light: #eef0f1;
    --mark-light-shade: #d9dcde;
    --backdrop: #2b2c2e;
    --on-navy: #e9eef1;
  }
  * { margin: 0; padding: 0; box-sizing: border-box; }
  html, body {
    width: 1200px;
    height: 732px;
    overflow: hidden;
    background: var(--backdrop);
    font-family: "Questrial", sans-serif;
  }
  .canvas {
    position: relative;
    width: 1200px;
    height: 732px;
  }
  .card {
    position: absolute;
    top: 242px;
    width: 436px;
    height: 248px;
    overflow: hidden;
  }
  .card--front {
    left: 144px;
    background: linear-gradient(135deg, var(--paper) 0%, #f8f8f8 45%, var(--paper-shade) 100%);
    color: var(--ink);
  }
  .card--back {
    left: 621px;
    background: linear-gradient(120deg, var(--navy) 0%, #073448 50%, var(--navy-deep) 100%);
  }
  .mark-area {
    position: absolute;
  }
  .card--front .mark-area {
    left: 329px;
    top: 35px;
    width: 107px;
    height: 213px;
    background: linear-gradient(160deg, var(--navy-soft) 0%, var(--navy) 100%);
  }
  .card--back .mark-area {
    left: 0;
    top: 0;
    width: 110px;
    height: 248px;
    background: linear-gradient(160deg, var(--mark-light) 0%, var(--mark-light-shade) 100%);
  }
  .wordmark {
    position: absolute;
    font-family: "Questrial", sans-serif;
    font-weight: 400;
    text-transform: uppercase;
    line-height: 1;
    white-space: nowrap;
  }
  .card--front .wordmark {
    left: 22px;
    top: 20px;
    font-size: 24px;
    letter-spacing: -0.01em;
    color: var(--navy);
  }
  .card--back .wordmark {
    right: 22px;
    top: 197px;
    font-size: 31px;
    letter-spacing: -0.01em;
    color: var(--on-navy);
  }
  .person {
    position: absolute;
    left: 22px;
    top: 115px;
  }
  .person__name {
    font-family: "Mulish", sans-serif;
    font-size: 18px;
    font-weight: 800;
    color: var(--navy);
    line-height: 1.05;
  }
  .person__role {
    font-size: 13px;
    line-height: 1.3;
    margin-top: 1px;
  }
  .contact {
    position: absolute;
    left: 22px;
    top: 161px;
    list-style: none;
    font-size: 13px;
    line-height: 14.5px;
  }
  .contact__label {
    display: inline-block;
    width: 19px;
    font-family: "Mulish", sans-serif;
    font-weight: 800;
    font-size: 11.5px;
    color: var(--navy);
  }
  .location {
    position: absolute;
    left: 22px;
    top: 216px;
    font-size: 13px;
  }
</style>
</head>
<body>
  <main class="canvas">
    <section class="card card--front" aria-label="Card front">
      <div class="wordmark">Maple Roster</div>
      <div class="person">
        <div class="person__name">Clara Whitfield</div>
        <div class="person__role">Director &nbsp;|&nbsp; Senior Search Consultant</div>
      </div>
      <ul class="contact">
        <li><span class="contact__label">T:</span> +64 27 000 4821</li>
        <li><span class="contact__label">E:</span> clara@mapleroster.nz</li>
        <li><span class="contact__label">W:</span> www.mapleroster.nz</li>
      </ul>
      <div class="location">Auckland, New Zealand</div>
      <div class="mark-area" role="img" aria-label="Large brand symbol, cropped at the card edge"></div>
    </section>

    <section class="card card--back" aria-label="Card back">
      <div class="mark-area" role="img" aria-label="Large brand symbol in light tone, cropped at the card edge"></div>
      <div class="wordmark">Maple Roster</div>
    </section>
  </main>
</body>
</html>
```